CM Candle Tube Packaging Design

Website: www.corvelmare.example
IG: @corvel.mare
Tagline: Elevate Your Ambiance
My brand is a sophisticated brand with luxury candles made of coconut wax. Im looking for an upscale minimalist chic design.
Discover the transformative power of positive energy with Corvel Mare candles. Indulge in true luxury with our specially crafted coconut wax blend that not only ignites captivating scents but also embodies modern elegance and empowering elements.
At Corvel Mare we're committed to delivering a unique and exhilarating aromatic experience to all candle lovers. Each candle is meticulously handcrafted in small batches using luxury fragrance oils exclusively formulated for coconut wax.
Our candles are:
Clean-burning
Paraben-Free
Phthalate-Free
Skin-Safe
Pet-Friendly

```html
<!DOCTYPE html>
<html lang="en">
<head>
<meta charset="utf-8">
<title>Corvel Mare – Candle Label</title>
<link href="https://fonts.googleapis.com/css2?family=Italiana&family=Montserrat:wght@400;600&family=Mrs+Saint+Delafield&display=swap" rel="stylesheet">
<style>
  :root {
    --page: #ffffff;
    --pattern: #d9d8cc;
    --sage: #c5c6b4;
    --frame-light: #ece8e3;
    --panel-blush: #fbf3ef;
    --panel-white: #ffffff;
    --ink: #1c1a1a;
    --ink-soft: #3a3636;
  }
  * { margin: 0; padding: 0; box-sizing: border-box; }
  html, body { width: 720px; height: 1200px; overflow: hidden; background: var(--page); }
  .canvas { position: relative; width: 720px; height: 1200px; }

  .label { position: absolute; left: 45px; top: 177px; width: 630px; height: 270px; }
  .label__pattern { position: absolute; inset: 0; background: var(--pattern); }
  .label__shapes { position: absolute; inset: 0; }

  .front { position: absolute; left: 233px; top: 58px; width: 164px; height: 156px; text-align: center; }
  .front__name {
    margin-top: 56px;
    font-family: "Italiana", serif;
    font-size: 17.5px; letter-spacing: 0.3px; color: var(--ink);
  }
  .front__sub {
    display: flex; align-items: center; justify-content: center; gap: 5px;
    margin-top: 3px;
    font-family: "Montserrat", sans-serif;
    font-size: 5.4px; letter-spacing: 1.6px; color: var(--ink-soft);
  }
  .front__sub::before, .front__sub::after {
    content: ""; width: 16px; height: 0.6px; background: var(--ink-soft);
  }
  .front__tag {
    margin-top: 2px;
    font-family: "Mrs Saint Delafield", cursive;
    font-size: 7px; color: var(--ink-soft);
  }

  .back { position: absolute; left: 506px; top: 42px; width: 112px; height: 186px; text-align: center; color: var(--ink); }
  .back__mark {
    margin-top: 22px;
    font-family: "Italiana", serif; font-size: 24px; letter-spacing: -1px;
  }
  .back__heading {
    margin-top: 16px;
    font-family: "Mrs Saint Delafield", cursive; font-size: 10px;
  }
  .back__list {
    list-style: none; margin: 1px auto 0; width: 58px; text-align: left;
    font-family: "Montserrat", sans-serif; font-weight: 600; font-size: 5.3px; line-height: 6.9px;
  }
  .back__list li::before { content: "•"; margin-right: 4px; }
  .back__slogan {
    margin-top: 4px;
    font-family: "Mrs Saint Delafield", cursive; font-size: 10px;
  }
  .back__contact {
    list-style: none; margin: 5px auto 0; width: 52px; text-align: left;
    font-family: "Montserrat", sans-serif; font-size: 3.8px; line-height: 6.5px;
  }
  .back__contact li { display: flex; align-items: center; gap: 2px; white-space: nowrap; }
  .back__dot { width: 4px; height: 4px; border-radius: 50%; background: var(--ink); flex: none; }
</style>
</head>
<body>
<main class="canvas">
  <section class="label">
    <div class="label__pattern" role="img" aria-label="Woven diagonal stripe pattern in sage and cream covering the label"></div>

    <svg class="label__shapes" width="630" height="270" viewBox="0 0 630 270">
      <polygon points="279,58 351,58 397,104 397,168 351,214 279,214 233,168 233,104"
               fill="var(--frame-light)" stroke="var(--sage)" stroke-width="3"/>
      <polygon points="281,64 349,64 391,106 391,166 349,208 281,208 239,166 239,106"
               fill="var(--panel-blush)" stroke="var(--sage)" stroke-width="2.5"/>
      <ellipse cx="562" cy="135" rx="56" ry="93" fill="var(--frame-light)" stroke="var(--sage)" stroke-width="2"/>
      <ellipse cx="562" cy="135" rx="51" ry="88" fill="var(--panel-white)" stroke="var(--sage)" stroke-width="1.5"/>
    </svg>

    <div class="front">
      <p class="front__name">CORVEL MARE</p>
      <p class="front__sub">HANDMADE CANDLES</p>
      <p class="front__tag">with purpose and love</p>
    </div>

    <div class="back">
      <p class="back__mark">CM</p>
      <p class="back__heading">Our Candles are:</p>
      <ul class="back__list">
        <li>Clean-burning</li>
        <li>Paraben-Free</li>
        <li>Phthalate-Free</li>
        <li>Skin-Safe</li>
        <li>Pet-Friendly</li>
      </ul>
      <p class="back__slogan">Elevate your ambience</p>
      <ul class="back__contact">
        <li><span class="back__dot"></span>www.corvelmare.example</li>
        <li><span class="back__dot"></span>@corvel.mare</li>
      </ul>
    </div>
  </section>
</main>
</body>
</html>
```